Chocolate Chip Cupcake package design

The cake is a branded packaged cupcake with chocolate chips on top and moist vanilla cake.

Our company is a baking company based in Middle East, producing high quality, European standard food snacks at an affordable price. We want a Clean, Modern and Trendy design - not too cluttered, colored yet not very busy, with a cupcake image (See attached for reference images).

Attached is Brindle Cupcake image - we feel it is clean but classic (we would like something more modern - this image is for your reference only, not as a guideline).

The Front side is 90 x 70mm. It will be a metallic packaging.

Target Market(s)

Teenagers, Adults - Lower, Middle and Upper Middle Class

Industry/Entity Type

It Company

Colors

Designer to choose colors to be used in the design.

Requirements
Must have
• Clean and a Modern - Appealing look
• "Choco Chip Cupcake" - product name
• Product photo
Should not have
• Too cluttered, busy background, very playful design.

```html
<!DOCTYPE html>
<html lang="en">
<head>
<meta charset="utf-8">
<title>Oatmeal Chocolate Chip Muffin – Pack Front</title>
<link rel="stylesheet" href="https://fonts.googleapis.com/css2?family=Marcellus&family=Philosopher:wght@700&display=swap">
<style>
  :root {
    --cocoa: #5e3a22;
    --cocoa-deep: #47291a;
    --cocoa-light: #7a5033;
    --cream: #ffffff;
    --silver: #e9e9ea;
    --silver-light: #f6f6f6;
    --crumb-light: #f1e2b8;
    --crumb: #e2c48a;
    --crust: #c98d45;
  }
  html, body {
    margin: 0;
    padding: 0;
    overflow: hidden;
    background: var(--silver-light);
  }
  .pack {
    position: relative;
    width: 935px;
    height: 1200px;
    overflow: hidden;
    background: linear-gradient(180deg, var(--silver-light) 0%, var(--silver) 100%);
  }
  .pack__waves {
    position: absolute;
    inset: 0;
  }
  .flavour-tab {
    position: absolute;
    left: 194px;
    top: 0;
    width: 547px;
    height: 300px;
    background: linear-gradient(180deg, var(--cocoa-light) 0%, var(--cocoa) 55%, var(--cocoa-deep) 100%);
    border-radius: 0 0 44px 44px;
    color: var(--cream);
    font-family: "Marcellus", serif;
    text-align: center;
  }
  .flavour-tab__main {
    position: absolute;
    top: 124px;
    left: 0;
    right: 0;
    font-size: 74px;
    line-height: 1;
    letter-spacing: 1px;
  }
  .flavour-tab__sub {
    position: absolute;
    top: 200px;
    left: 0;
    right: 0;
    font-size: 49px;
    line-height: 1;
  }
  .product-name {
    position: absolute;
    top: 318px;
    left: 0;
    width: 935px;
    margin: 0;
    text-align: center;
    font-family: "Philosopher", sans-serif;
    font-weight: 700;
    font-size: 168px;
    line-height: 1;
    color: var(--cocoa);
    text-shadow: 0 0 3px #f1d9b6, 0 2px 2px rgba(0,0,0,.15);
  }
  .product-photo {
    position: absolute;
    left: 150px;
    top: 584px;
    width: 645px;
    height: 576px;
    border-radius: 40px;
    background: radial-gradient(ellipse at 50% 35%, var(--crumb-light) 0%, var(--crumb) 55%, var(--crust) 100%);
  }
  .claim-ribbon {
    position: absolute;
    left: 618px;
    top: 1012px;
    width: 340px;
    height: 82px;
    background: var(--cocoa);
    transform: rotate(8deg);
    transform-origin: left center;
    clip-path: polygon(0 0, 100% 0, 100% 100%, 0 100%, 5% 50%);
    color: var(--cream);
    font-family: "Philosopher", sans-serif;
    font-weight: 700;
    font-size: 44px;
    line-height: 82px;
    padding-left: 46px;
    box-sizing: border-box;
    white-space: nowrap;
  }
</style>
</head>
<body>
<main class="pack">
  <svg class="pack__waves" width="935" height="1200" viewBox="0 0 935 1200" aria-hidden="true">
    <defs>
      <linearGradient id="bandFill" x1="0" y1="0" x2="1" y2="1">
        <stop offset="0" stop-color="#6a4329"/>
        <stop offset="1" stop-color="#4a2b1b"/>
      </linearGradient>
    </defs>
    <path d="M0 470 C250 420 520 520 935 420 L935 470 C560 560 260 470 0 520 Z" fill="#e0e0e2"/>
    <path d="M0 560 C260 510 600 580 935 455 L935 830 C760 880 560 760 300 840 C150 890 60 1010 40 1200 L0 1200 Z" fill="url(#bandFill)"/>
    <path d="M0 560 C260 510 600 580 935 455 L935 475 C600 600 260 535 0 585 Z" fill="#ffffff" opacity=".25"/>
    <path d="M40 1200 C60 1010 150 890 300 840 C560 760 760 880 935 830 L935 870 C760 920 560 820 320 880 C180 930 100 1040 90 1200 Z" fill="#ffffff"/>
  </svg>

  <header class="flavour-tab">
    <div class="flavour-tab__main">OATMEAL</div>
    <div class="flavour-tab__sub">Chocolate Chip</div>
  </header>

  <h1 class="product-name">Muffin</h1>

  <div class="product-photo" role="img" aria-label="Product photo: oatmeal chocolate chip muffin in a paper baking case"></div>

  <div class="claim-ribbon">0 trans fat</div>
</main>
</body>
</html>
```